Biz Card

MARKETING today is the most rapidly changing business discipline. Media options to reach customers, actual customer preferences and consumer buying decisions change by the minute . . . no, by the second. The behavioral data generated by all aspects of the business and the new technologies that put the data to work together produce the potential to generate business intelligence and guide smart resource allocation to influence purchase and retention. However, to realize this potential, marketing professionals at all levels and in all organizations must continuously improve their skills not just from on-the-job training but by learning from masters in the field. The Bright Horizon Guild is the training center that serves this professional development need.model logos:msi.orgama.orgcontentmarketinginstitute.comBook covers on MarketingMetrics, Marketing Anaytics
Industry/Entity Type
Business
Contact Information for Business Card
Roy A. YoungCEOMarketing Science Academyphone: 310-601-4755email: roy@marketingscience.comAddress:437 South Rexford DriveBeverly Hills, CA 89377
Look and feel
Each slider illustrates characteristics of the customer's brand and the style your logo design should communicate.

```html
<!DOCTYPE html>
<html lang="en">
<head>
<meta charset="utf-8">
<title>Bright Horizon Guild — Business Card</title>
<link href="https://fonts.googleapis.com/css2?family=Roboto:wght@400;700;900&family=Roboto+Condensed:wght@700&display=swap" rel="stylesheet">
<style>
  :root {
    --backdrop: #b3b1b1;
    --card: #fbfbfb;
    --brand-red: #8e2522;
    --ink-gray: #555354;
    --text-gray: #5a5a5a;
  }
  * { margin: 0; padding: 0; box-sizing: border-box; }
  html, body { width: 1200px; height: 1200px; overflow: hidden; }
  body {
    background: var(--backdrop);
    position: relative;
    font-family: "Roboto", Arial, sans-serif;
  }
  .card {
    position: absolute;
    background: var(--card);
    overflow: hidden;
  }
  .card-front { left: 238px; top: 119px; width: 714px; height: 418px; }
  .card-back  { left: 230px; top: 645px; width: 712px; height: 416px; }

  .front-band {
    position: absolute; left: 0; right: 0; bottom: 0; height: 16px;
    background: var(--brand-red);
  }
  .front-mark {
    position: absolute; left: 0; right: 0; top: 160px;
    display: flex; align-items: center; justify-content: center; gap: 22px;
  }
  .mark-dot {
    width: 58px; height: 58px; border-radius: 50%;
    background: var(--brand-red);
  }
  .mark-name {
    font-family: "Roboto Condensed", Arial, sans-serif;
    font-weight: 700;
    color: var(--ink-gray);
    text-transform: uppercase;
    line-height: 1;
  }
  .front-mark .mark-name { font-size: 30px; line-height: 31px; }

  .back-mark {
    position: absolute; left: 78px; top: 112px; width: 265px;
    display: flex; flex-direction: column; align-items: flex-start; gap: 18px;
  }
  .back-mark .mark-dot { width: 70px; height: 70px; }
  .back-mark .mark-name { font-size: 36px; line-height: 38px; }

  .contact {
    position: absolute; left: 410px; top: 100px;
    color: var(--text-gray);
  }
  .contact-name {
    font-family: "Roboto Condensed", Arial, sans-serif;
    font-weight: 700; font-size: 25px; color: var(--brand-red);
  }
  .contact-role { font-size: 14px; letter-spacing: 1px; margin-top: 10px; }
  .contact-address { font-size: 17px; line-height: 24px; margin-top: 28px; }
  .contact-lines { list-style: none; margin-top: 6px; font-size: 17px; line-height: 24px; }
  .contact-lines li { display: flex; align-items: center; gap: 18px; }
  .contact-lines svg { width: 17px; height: 14px; fill: var(--brand-red); flex: none; }
</style>
</head>
<body>
  <section class="card card-front" aria-label="Card front">
    <div class="front-mark">
      <span class="mark-dot" aria-hidden="true"></span>
      <div class="mark-name">Bright<br>Horizon<br>Guild</div>
    </div>
    <div class="front-band"></div>
  </section>

  <section class="card card-back" aria-label="Card back">
    <div class="back-mark">
      <span class="mark-dot" aria-hidden="true"></span>
      <div class="mark-name">Bright Horizon<br>Guild</div>
    </div>
    <div class="contact">
      <p class="contact-name">Neil P. Barton</p>
      <p class="contact-role">CEO</p>
      <p class="contact-address">912 North Calloway Lane<br>Beverly Hills, CA 89377</p>
      <ul class="contact-lines">
        <li>
          <svg viewBox="0 0 17 14" aria-hidden="true"><path d="M1 4c0-2 3-3 7.5-3S16 2 16 4v1h-4V3.5H5V5H1z"/><path d="M3 6h11l1 7H2z"/></svg>
          310-555-0182
        </li>
        <li>
          <svg viewBox="0 0 17 14" aria-hidden="true"><path d="M1 2h15v10H1z M2.5 3.5l6 5 6-5v-.1H2.5z" fill-rule="evenodd"/></svg>
          neil@brighthorizonguild.com
        </li>
        <li>
          <svg viewBox="0 0 17 14" aria-hidden="true"><circle cx="8.5" cy="7" r="6.5"/><path d="M2 7h13M8.5 .5v13" stroke="#fbfbfb" stroke-width="1.2"/></svg>
          www.brighthorizonguild.com
        </li>
      </ul>
    </div>
  </section>
</body>
</html>
```